I just need to get that same logo on the business card but with different word. “The Hinges Roadside and Rental”

Name: Marek T
Number: 4759028416
Email: thehingesroadside@brivomail.test

On the back, can we di just the logo and the hinges roadside and rental around it.

If possible a black card with the gold storefront type font that you used before, would be amazing. I attached the original logo just in case.

Target Market(s)

Roadside assistance

Industry/Entity Type

Repair/ roadside

Contact Information for Business Card

Name, email, phone number

Requirements
Must have
• Everything in description
Nice to have
• Nice big logo

```html
<!DOCTYPE html>
<html lang="en">
<head>
<meta charset="utf-8">
<title>The Hinges Roadside and Rental — Business Card</title>
<link href="https://fonts.googleapis.com/css2?family=Montserrat:wght@400;700&display=swap" rel="stylesheet">
<style>
  :root {
    --backdrop: #1d1d1f;
    --card: #131314;
    --card-edge: #2a2a2c;
    --gold: #b48f4f;
    --gold-soft: #a5844a;
  }
  * { box-sizing: border-box; margin: 0; padding: 0; }
  html, body {
    width: 1200px;
    height: 857px;
    overflow: hidden;
    background: var(--backdrop);
  }
  .canvas {
    width: 1200px;
    height: 857px;
    display: flex;
    flex-direction: column;
    align-items: center;
    justify-content: center;
    gap: 56px;
  }
  .card {
    width: 560px;
    height: 320px;
    background: var(--card);
    border: 1px solid var(--card-edge);
    border-radius: 3px;
    position: relative;
    box-shadow: 0 18px 40px rgba(0,0,0,0.45);
    color: var(--gold);
    font-family: "Montserrat", sans-serif;
  }

  /* Front: large centred wordmark */
  .card--front {
    display: flex;
    flex-direction: column;
    align-items: center;
    justify-content: center;
  }
  .brand-square {
    width: 58px;
    height: 58px;
    background: var(--gold);
    margin-bottom: 22px;
  }
  .brand-name {
    font-weight: 700;
    color: var(--gold);
    text-align: center;
    line-height: 1.1;
  }
  .brand-name__main {
    display: block;
    font-size: 44px;
    letter-spacing: 1px;
  }
  .brand-name__sub {
    display: block;
    font-size: 15px;
    letter-spacing: 2.4px;
    margin-top: 6px;
  }

  /* Back: wordmark left, contact right */
  .card--back {
    display: flex;
    align-items: center;
    padding: 0 40px;
  }
  .card--back .brand {
    display: flex;
    flex-direction: column;
    align-items: center;
    width: 240px;
    margin-top: 60px;
  }
  .card--back .brand-square {
    width: 36px;
    height: 36px;
    margin-bottom: 14px;
  }
  .card--back .brand-name__main { font-size: 27px; letter-spacing: 0.5px; }
  .card--back .brand-name__sub { font-size: 9.5px; letter-spacing: 1.5px; margin-top: 4px; }

  .contact {
    margin-left: 28px;
    margin-top: -30px;
  }
  .contact__name {
    font-weight: 700;
    font-size: 27px;
    letter-spacing: 2px;
    margin-bottom: 26px;
    text-align: center;
  }
  .contact__line {
    font-weight: 400;
    font-size: 13px;
    letter-spacing: 0.6px;
    color: var(--gold-soft);
    margin-bottom: 14px;
  }
</style>
</head>
<body>
  <main class="canvas">
    <section class="card card--front" aria-label="Business card front">
      <div class="brand-square" aria-hidden="true"></div>
      <h1 class="brand-name">
        <span class="brand-name__main">THE HINGES</span>
        <span class="brand-name__sub">ROADSIDE AND RENTAL</span>
      </h1>
    </section>

    <section class="card card--back" aria-label="Business card back">
      <div class="brand">
        <div class="brand-square" aria-hidden="true"></div>
        <p class="brand-name">
          <span class="brand-name__main">THE HINGES</span>
          <span class="brand-name__sub">ROADSIDE AND RENTAL</span>
        </p>
      </div>
      <div class="contact">
        <p class="contact__name">MAREK T</p>
        <p class="contact__line">4759028416</p>
        <p class="contact__line">thehingesroadside@brivomail.test</p>
      </div>
    </section>
  </main>
</body>
</html>
```